Communication and Marketing agency needs a new presentation card

We are a group of communication and marketing agencies specialized in companies that are in the logistics and industrial sector. The head agency is TELVANO Grupo and the group consists of 4 agencies: TELVANO Media, TELVANO Digital, TELVANO Research and DifundeEnPantalla. We hace 4 offices in Spain (Madrid, Barcelona, Valencia and Murcia). We are looking for a clean and attractive design that transmits our experience, brand presence in the market and knowledge to those who receive the card.It has to maintain the colors of the logo that is attached.
Target Market(s)
logistics and industrial sector
Marketing department
Contact Information for Business Card
Clean and attractive design

```html
<!DOCTYPE html>
<html lang="en">
<head>
<meta charset="utf-8">
<title>TELVANO Grupo – Business Card</title>
<link rel="stylesheet" href="https://fonts.googleapis.com/css2?family=Oswald:wght@400;500&family=PT+Sans:ital,wght@0,400;1,700&display=swap">
<style>
  :root {
    --brand-red: #b3212b;
    --brand-grey: #4d4d4d;
    --ink: #2b2b2b;
    --ink-soft: #555555;
    --paper: #ffffff;
    --backdrop: #ececec;
    --map-tone: #f0f0f0;
  }
  html, body {
    margin: 0;
    width: 1200px;
    height: 1200px;
    overflow: hidden;
    background: var(--backdrop);
  }
  .card {
    position: absolute;
    left: 223px;
    width: 815px;
    height: 466px;
    background: var(--paper);
    overflow: hidden;
  }
  .card--front { top: 76px; }
  .card--back { top: 658px; }

  .wordmark {
    position: absolute;
    font-family: "Oswald", sans-serif;
    font-weight: 400;
    text-align: right;
    line-height: 1;
  }
  .wordmark__main {
    display: block;
    color: var(--brand-red);
    font-size: 84px;
    letter-spacing: 0.31em;
    margin-right: -0.31em;
  }
  .wordmark__sub {
    display: block;
    color: var(--brand-grey);
    font-size: 64px;
    font-weight: 500;
    margin-top: -2px;
  }
  .card--front .wordmark { right: 64px; top: 64px; }
  .card--back .wordmark { right: 186px; top: 150px; }

  .person {
    position: absolute;
    left: 72px;
    top: 264px;
  }
  .person__name {
    margin: 0;
    font-family: "Oswald", sans-serif;
    font-weight: 500;
    font-size: 36px;
    line-height: 1;
    color: var(--brand-red);
  }
  .person__role {
    margin: 6px 0 0;
    font-family: "PT Sans", sans-serif;
    font-size: 19px;
    letter-spacing: 0.02em;
    color: var(--ink);
  }

  .marker {
    display: block;
    margin: 12px 0 10px;
  }

  .details {
    position: absolute;
    font-family: "PT Sans", sans-serif;
    font-size: 18.5px;
    line-height: 23.5px;
    color: var(--ink);
  }
  .details p { margin: 0; }
  .details--contact { left: 72px; top: 318px; }
  .details--address { left: 554px; top: 314px; }
  .label { color: var(--brand-red); }
  .accent { color: var(--brand-red); }

  .world-map {
    position: absolute;
    inset: 0;
    background: linear-gradient(180deg, var(--map-tone) 0%, #f6f6f6 60%, var(--paper) 100%);
  }

  .site-link {
    position: absolute;
    left: 0;
    right: 0;
    top: 408px;
    margin: 0;
    text-align: center;
    font-family: "PT Sans", sans-serif;
    font-style: italic;
    font-weight: 700;
    font-size: 22px;
    color: var(--ink-soft);
  }
  .site-link .arrows { color: var(--brand-red); margin: 0 10px; }
</style>
</head>
<body>

<section class="card card--front">
  <div class="wordmark">
    <span class="wordmark__main">TELVANO</span>
    <span class="wordmark__sub">Grupo</span>
  </div>

  <div class="person">
    <h1 class="person__name">MARCO ELLISON</h1>
    <p class="person__role">MANAGER &amp; CEO</p>
  </div>

  <div class="details details--contact">
    <svg class="marker" width="38" height="8" viewBox="0 0 38 8" aria-hidden="true">
      <circle cx="4" cy="4" r="3.5" fill="#b3212b"/>
      <line x1="4" y1="4" x2="38" y2="4" stroke="#b3212b" stroke-width="1.5"/>
    </svg>
    <p><span class="label">P.</span> +(402) 555-0148</p>
    <p><span class="label">F.</span> +(402) 555-0149</p>
    <p>hello@telvanomail.com</p>
  </div>

  <div class="details details--address">
    <svg class="marker" width="38" height="8" viewBox="0 0 38 8" aria-hidden="true">
      <circle cx="4" cy="4" r="3.5" fill="#b3212b"/>
      <line x1="4" y1="4" x2="38" y2="4" stroke="#b3212b" stroke-width="1.5"/>
    </svg>
    <p>48 Calle Norte Azul,</p>
    <p>Valverde 28410</p>
    <p>www.<span class="accent">telvanogroup</span>.com</p>
  </div>
</section>

<section class="card card--back">
  <div class="world-map" role="img" aria-label="Faint dotted world map in light grey filling the card background"></div>

  <div class="wordmark">
    <span class="wordmark__main">TELVANO</span>
    <span class="wordmark__sub">Grupo</span>
  </div>

  <p class="site-link"><span class="arrows">&gt;&gt;</span>www.telvano.com<span class="arrows">&lt;&lt;</span></p>
</section>

</body>
</html>
```